Redesign of an existing homepage

This site needs a redesign
https://www.wanderhof-kelbach.de
This page with the accommodation options is important for the customer
https://www.wanderhof-kelbach.de/gastgeber/
Till now there is a new logo. See attachment. That's all I have.
It would make sense to use the colors of the logo in the redesign.
footer.jpg.
I would put this info into the footer. The graphic (Infomaterial) is not needed.
a new menu - links.jpg
This info can be put in a new menu. Therefore the right column is gone and there is more space for the design.
NEW:
Please keep in mind that the Icons are important and shall be displayed under every accommodation

```html
<!DOCTYPE html>
<html lang="de">
<head>
<meta charset="utf-8">
<title>Tourismusverband Kelbach – Urlaub im Kelbachtal</title>
<link href="https://fonts.googleapis.com/css2?family=Montserrat:wght@400;500;600;700&family=Roboto:wght@500;700;900&display=swap" rel="stylesheet">
<style>
:root{
  --blue:#1d58a7;
  --blue-dark:#164a8f;
  --sky:#2b93d8;
  --green:#6aac1f;
  --green-light:#8fc63f;
  --pale:#eaf5fd;
  --text:#222;
  --teal:#2aa6c9;
  --white:#fff;
}
*{margin:0;padding:0;box-sizing:border-box}
html,body{width:1200px;height:5080px;overflow:hidden}
body{position:relative;background:var(--white);font-family:"Montserrat",sans-serif;color:var(--text)}
.abs{position:absolute}

/* header */
.brand{left:110px;top:36px;width:220px;text-align:center}
.brand .mark{width:74px;height:74px;border-radius:50%;background:var(--green);margin:0 auto 8px}
.brand .name{font-family:"Montserrat",sans-serif;font-weight:700;color:var(--blue);font-size:18px;line-height:22px}
.topbar{left:450px;top:28px;width:640px;height:50px;display:flex;align-items:center;gap:34px}
.lang{font-size:14px;font-weight:600;display:flex;align-items:center;gap:6px}
.badge{height:46px;border-radius:6px;background:#dfe7ef}
.badge.round{width:46px;border-radius:50%;background:#cfe3a8}
.nav{left:395px;top:100px;width:805px;height:68px;background:var(--blue);border-radius:34px 0 0 34px;display:flex;align-items:center;padding-left:14px}
.nav a{color:var(--white);text-decoration:none;font-size:14px;font-weight:500;margin-right:42px;text-transform:uppercase}
.nav a.active{background:var(--green);padding:14px 30px;border-radius:28px;font-weight:700;margin-right:16px}

/* hero */
.hero-bg{left:0;top:0;width:1200px;height:740px}
.hero-title{left:108px;top:266px;font-family:"Roboto",sans-serif;font-weight:700;font-size:49px;line-height:56px;color:#111;text-transform:uppercase}
.hero-title .hl{color:var(--blue)}
.hero-copy{left:110px;top:442px;width:410px;font-size:15px;line-height:31px;color:#222}
.btn{display:inline-block;border-radius:30px;color:var(--white);font-weight:700;text-transform:uppercase;font-size:14px;text-align:center;text-decoration:none}
.btn-green{background:var(--green);box-shadow:0 0 0 4px rgba(255,255,255,.6)}
.btn-blue{background:var(--blue)}
.hero-btn{left:110px;top:582px;width:164px;height:50px;line-height:50px}
.hero-emblem{left:562px;top:656px;width:76px;height:76px;border-radius:50%;background:var(--white);border:5px solid var(--green-light)}
.hero-emblem span{display:block;width:40px;height:40px;border-radius:50%;background:var(--green);margin:13px auto}

/* section heads */
.sec-dot{width:40px;height:40px;border-radius:50%;background:var(--green);left:580px}
.sec-title{left:0;width:1200px;text-align:center;font-family:"Roboto",sans-serif;font-weight:700;font-size:43px;color:var(--blue);text-transform:uppercase}
.sec-sub{left:0;width:1200px;text-align:center;font-family:"Roboto",sans-serif;font-weight:500;font-size:19px;color:#222;text-transform:uppercase}
.intro{left:130px;width:940px;text-align:center;font-size:15px;line-height:31px}
.video{left:166px;top:1269px;width:870px;height:400px;border-radius:20px;background:linear-gradient(180deg,#4a5e8a 0%,#7f7a8c 45%,#a88e82 75%,#6f5d58 100%)}
.play{left:572px;top:1440px;width:58px;height:58px;border-radius:50%;background:var(--green);box-shadow:0 0 0 6px rgba(255,255,255,.5)}

/* hosts */
.hosts-bg{left:0;top:1780px;width:1200px;height:2040px}
.host-photo{width:426px;height:426px;border-radius:50%}
.ring{width:470px;height:470px}
.host-title{font-family:"Roboto",sans-serif;font-weight:700;font-size:28px;color:#111;text-transform:uppercase}
.host-text{width:420px;font-size:15px;line-height:29px}
.host-text p+p{margin-top:29px}
.loc{font-size:15px;line-height:29px}
.loc b{color:var(--teal);font-weight:500}
.amen{display:flex;gap:30px;font-size:15px;align-items:center}
.amen span{display:flex;align-items:center;gap:12px}
.price{font-family:"Roboto",sans-serif;font-weight:700;font-size:19px;color:var(--blue);text-transform:uppercase}
.details{width:262px;height:52px;line-height:52px;font-size:14px}
.more{left:458px;top:3670px;width:284px;height:56px;line-height:56px}

/* gallery */
.tile{border-radius:2px}

/* footer */
.footer-bg{left:0;top:4600px;width:1200px;height:480px}
.f-brand{left:110px;top:4760px;width:280px;text-align:center}
.f-brand .mark{width:104px;height:104px;border-radius:50%;background:var(--white);margin:0 auto 18px;opacity:.95}
.f-brand .name{font-weight:700;font-size:25px;line-height:30px;color:var(--white)}
.f-contact{left:503px;top:4752px;color:var(--white);font-size:14px;line-height:31px}
.f-contact h4{font-family:"Roboto",sans-serif;font-weight:700;font-size:18px;margin-bottom:6px;text-transform:uppercase}
.f-assoc{left:835px;top:4756px;width:270px;color:var(--white);font-size:14px;line-height:31px}
.f-rule{left:110px;top:4997px;width:980px;height:1px;background:rgba(255,255,255,.55)}
.f-copy{left:0;top:5033px;width:1200px;text-align:center;color:var(--white);font-size:14px}
</style>
</head>
<body>

<!-- hero -->
<svg class="abs hero-bg" viewBox="0 0 1200 740" role="img" aria-label="Fotografie: lachende Mutter mit zwei Kindern auf einer sonnigen Wiese">
  <defs>
    <linearGradient id="heroFill" x1="0" y1="0" x2="1" y2="0.3">
      <stop offset="0" stop-color="#f4f1e2"/>
      <stop offset="0.35" stop-color="#eee5c2"/>
      <stop offset="0.6" stop-color="#c9b58f"/>
      <stop offset="1" stop-color="#9fb57a"/>
    </linearGradient>
    <linearGradient id="grass" x1="0" y1="0" x2="0" y2="1">
      <stop offset="0" stop-color="#c7b742" stop-opacity="0"/>
      <stop offset="1" stop-color="#8a9a2a"/>
    </linearGradient>
  </defs>
  <path d="M0 0H1200V690Q900 650 600 720Q300 650 0 690Z" fill="url(#heroFill)"/>
  <path d="M0 500H1200V690Q900 650 600 720Q300 650 0 690Z" fill="url(#grass)"/>
  <path d="M0 690Q300 650 600 720Q900 650 1200 690" fill="none" stroke="#8fc63f" stroke-width="4"/>
  <circle cx="810" cy="410" r="250" fill="none" stroke="#b7d98a" stroke-width="10" opacity=".7" stroke-dasharray="700 900"/>
</svg>

<div class="abs brand"><div class="mark"></div><div class="name">TOURISMUSVERBAND<br>KELBACH</div></div>

<div class="abs topbar">
  <div class="lang">
    <svg width="18" height="18" viewBox="0 0 20 20" fill="none" stroke="#222" stroke-width="1.6"><circle cx="10" cy="10" r="8"/><path d="M2 10h16M10 2c3 3 3 13 0 16M10 2c-3 3-3 13 0 16"/></svg>
    EN
    <svg width="10" height="10" viewBox="0 0 10 10"><path d="M1 3l4 4 4-4" stroke="#222" stroke-width="1.6" fill="none"/></svg>
  </div>
  <div class="badge" style="width:66px"></div>
  <div class="badge round"></div>
  <div class="badge" style="width:150px"></div>
  <div class="badge" style="width:136px"></div>
</div>

<nav class="abs nav">
  <a class="active" href="https://www.wanderhof-kelbach.de">Heim</a>
  <a href="https://www.wanderhof-kelbach.de/gastgeber/">Gastgeber</a>
  <a href="#">Kelbachtal</a>
  <a href="#">Freizeit</a>
  <a href="#">Ausflugsziele</a>
  <a href="#">Kontakt</a>
</nav>

<h1 class="abs hero-title"><span class="hl">Urlaub im Kelbachtal<br>- dem</span> schönsten<br>Fleck Bayerns</h1>
<p class="abs hero-copy">Kelbach und Umgebung haben all das, was das Leben lebenswert macht: Kultur und Natur, Lebensfreude und Genuss, freundliche und aufgeschlossene Menschen</p>
<a class="abs btn btn-green hero-btn" href="#">Jetzt buchen</a>
<div class="abs hero-emblem"><span></span></div>

<!-- welcome -->
<div class="abs sec-dot" style="top:815px"></div>
<h2 class="abs sec-title" style="top:866px">Willkommen bei Tourismusverband</h2>
<div class="abs sec-sub" style="top:932px">Kelbach</div>
<div class="abs intro" style="top:974px">
  <p>Kelbach und Umgebung haben all das, was das Leben lebenswert macht: Kultur und Natur, Lebensfreude und Genuss, freundliche und aufgeschlossene Menschen… Ob Kirchen, Brunnen oder andere Baudenkmäler – bei einem Rundgang durch die Kelbacher Mühlenstadt kann man viele liebevolle Details für sich entdecken.</p>
  <p style="margin-top:31px">Für Bewegungsfreudige und Erholungssuchende gibt es “Natur pur” in und um Kelbach! Hier kann man sportlich unterwegs sein beim Radeln, Walken, Wandern, Golfen, Reiten und Baden oder einfach nur die Ruhe genießen. Freizeit und Erholung für die ganze Familie – planen Sie einen Urlaub auf dem Bauernhof, in einer Ferienwohnung oder im Hotel. Ihr Urlaub im Kelbachtal wird ein einmaliges Erlebnis!</p>
</div>
<div class="abs video" role="img" aria-label="Videovorschau: Stadtplatz mit Rathausturm in der Dämmerung"></div>
<div class="abs play"><svg width="58" height="58" viewBox="0 0 58 58"><path d="M23 18l16 11-16 11z" fill="#fff"/></svg></div>

<!-- hosts -->
<svg class="abs hosts-bg" viewBox="0 0 1200 2040" preserveAspectRatio="none">
  <path d="M0 20Q300 -15 600 25Q900 -15 1200 20V2000Q900 2040 600 1990Q300 2040 0 2000Z" fill="#eaf5fd"/>
</svg>

<div class="abs sec-dot" style="top:1866px"></div>
<h2 class="abs sec-title" style="top:1918px">Gastgeber im Kelbachtal</h2>
<div class="abs sec-sub" style="top:1986px">Dienstleistungen</div>

<svg width="0" height="0" style="position:absolute">
  <defs>
    <symbol id="bed" viewBox="0 0 24 18"><path d="M1 3h2v6h18a2 2 0 0 1 2 2v6h-2v-2H3v2H1z" fill="#111"/><rect x="4" y="5" width="6" height="4" rx="1" fill="#111"/><rect x="11" y="4" width="10" height="5" rx="1" fill="#111"/></symbol>
    <symbol id="car" viewBox="0 0 26 20"><path d="M5 3h16l3 7v8h-3v-2H5v2H2v-8z" fill="#111"/><rect x="7" y="5" width="12" height="5" fill="#fff"/><circle cx="7" cy="13" r="1.6" fill="#fff"/><circle cx="19" cy="13" r="1.6" fill="#fff"/></symbol>
  </defs>
</svg>

<!-- host 1 -->
<svg class="abs ring" style="left:110px;top:2075px" viewBox="0 0 470 470"><circle cx="235" cy="235" r="225" fill="none" stroke="#6aac1f" stroke-width="14" stroke-dasharray="760 1500" transform="rotate(160 235 235)"/><circle cx="235" cy="235" r="222" fill="none" stroke="#2b93d8" stroke-width="12" stroke-dasharray="430 1500" transform="rotate(-20 235 235)"/></svg>
<div class="abs host-photo" style="left:132px;top:2097px;background:linear-gradient(180deg,#8fb4d4 0%,#3c2f26 35%,#5b4a3a 70%,#6e8a3a 100%)" role="img" aria-label="Fotografie: dunkles Holzhaus mit Balkon und Gartenzaun"></div>
<div class="abs" style="left:661px;top:2106px">
  <h3 class="host-title">Lindenhof</h3>
  <div class="host-text" style="margin-top:10px"><p>Bei uns erwartet Sie ein unvergesslicher, erholsamer und ruhiger Urlaub für die ganze Familie. Unser Landhaus liegt idyllisch zwischen Wald und Wiesen.</p><p>In der Nähe eines wunderbaren Naherholungsgebietes Kelbacher Auensee.</p></div>
  <div class="loc"><b>Standort:</b> Am Anger 4, 84399 Kelbach 1 Wohneinheit</div>
  <div class="amen" style="margin-top:14px"><span><svg width="26" height="20"><use href="#bed"/></svg>Bett</span><span><svg width="28" height="22"><use href="#car"/></svg>Auto</span></div>
  <div class="price" style="margin-top:22px">Aus € 59.00</div>
  <a class="btn btn-blue details" style="margin-top:24px" href="https://www.wanderhof-kelbach.de/gastgeber/">Weitere Details anzeigen</a>
</div>

<!-- host 2 -->
<div class="abs" style="left:110px;top:2638px">
  <h3 class="host-title">Parkhotel Kelbach</h3>
  <div class="host-text" style="margin-top:10px"><p>Im Herzen Kelbachs erwartet Sie unser neues Hotel mit 22 modern ausgestatteten Zimmern. Ankommen und einfach wohlfühlen!</p><p>Ob Businesstermin, Durchreise oder Urlaub im Kelbachtal, bei uns sind Sie richtig aufgehoben.</p></div>
  <div class="loc"><b>Standort:</b> Marktplatz 7, 84398 Kelbach</div>
  <div class="amen" style="margin-top:14px"><span><svg width="26" height="20"><use href="#bed"/></svg>Bett</span><span><svg width="28" height="22"><use href="#car"/></svg>Auto</span></div>
  <div class="price" style="margin-top:22px">Ab € 59,00</div>
  <a class="btn btn-blue details" style="margin-top:24px" href="https://www.wanderhof-kelbach.de/gastgeber/">Weitere Details anzeigen</a>
</div>
<svg class="abs ring" style="left:628px;top:2608px" viewBox="0 0 470 470"><circle cx="235" cy="235" r="225" fill="none" stroke="#6aac1f" stroke-width="14" stroke-dasharray="760 1500" transform="rotate(160 235 235)"/><circle cx="235" cy="235" r="222" fill="none" stroke="#2b93d8" stroke-width="12" stroke-dasharray="430 1500" transform="rotate(-20 235 235)"/></svg>
<div class="abs host-photo" style="left:650px;top:2630px;background:linear-gradient(135deg,#f1ede6 0%,#cfc4b4 40%,#8a6a4c 70%,#e7e1d8 100%)" role="img" aria-label="Fotografie: modernes Wohnzimmer mit Sofa und rundem Couchtisch"></div>

<!-- host 3 -->
<svg class="abs ring" style="left:110px;top:3150px" viewBox="0 0 470 470"><circle cx="235" cy="235" r="225" fill="none" stroke="#6aac1f" stroke-width="14" stroke-dasharray="760 1500" transform="rotate(160 235 235)"/><circle cx="235" cy="235" r="222" fill="none" stroke="#2b93d8" stroke-width="12" stroke-dasharray="430 1500" transform="rotate(-20 235 235)"/></svg>
<div class="abs host-photo" style="left:132px;top:3172px;background:linear-gradient(180deg,#2f6fc0 0%,#dfe8f2 45%,#b98a6a 70%,#5f8aa0 100%)" role="img" aria-label="Fotografie: Flussufer mit bunten Häusern und Kirchturm unter Wolkenhimmel"></div>
<div class="abs" style="left:661px;top:3176px">
  <h3 class="host-title">Auencamp Kelbach</h3>
  <div class="host-text" style="margin-top:10px"><p>Camping für alle Generationen. Das Auencamp Kelbach ist ein ideales Reiseziel für Erholungssuchende, Wellness-Freunde, Aktivurlauber sowie Familien mit Kindern. Umgeben von weiten Feldern und bewaldeten Hügeln laden gleich drei Naturseen zum erfrischenden Badespaß ein.</p></div>
  <div class="loc"><b>Standort:</b> Auweg 12, 84397 Kelbach</div>
  <div class="amen" style="margin-top:14px"><span><svg width="26" height="20"><use href="#bed"/></svg>Bett</span><span><svg width="28" height="22"><use href="#car"/></svg>Auto</span></div>
  <div class="price" style="margin-top:22px">Ab € 23,90 für 2 Personen</div>
  <a class="btn btn-blue details" style="margin-top:24px" href="https://www.wanderhof-kelbach.de/gastgeber/">Weitere Details anzeigen</a>
</div>

<a class="abs btn btn-green more" href="https://www.wanderhof-kelbach.de/gastgeber/">Weitere Services anzeigen</a>

<!-- portfolio -->
<div class="abs sec-dot" style="top:3908px"></div>
<h2 class="abs sec-title" style="top:3960px">Unser Portfolio</h2>
<div class="abs sec-sub" style="top:4026px">Galerie</div>
<div class="abs tile" style="left:110px;top:4092px;width:326px;height:434px;background:linear-gradient(180deg,#6aa5dc 0%,#d9b77a 40%,#9a5b3e 70%,#7b7670 100%)" role="img" aria-label="Fotografie: Altstadtgasse mit bunten Giebelhäusern"></div>
<div class="abs tile" style="left:446px;top:4092px;width:316px;height:268px;background:linear-gradient(135deg,#f2f2f0 0%,#d8d8d4 50%,#a9a49a 100%)" role="img" aria-label="Fotografie: helles Zimmer mit Sessel und Zimmerpflanze"></div>
<div class="abs tile" style="left:446px;top:4368px;width:316px;height:158px;background:linear-gradient(180deg,#e6e6e6 0%,#bdbdbd 50%,#3a3a3a 100%)" role="img" aria-label="Fotografie: moderne Küche mit Esstisch"></div>
<div class="abs tile" style="left:772px;top:4092px;width:318px;height:434px;background:linear-gradient(180deg,#f4f4f2 0%,#8c6a55 35%,#a5553d 60%,#5d8a3a 100%)" role="img" aria-label="Fotografie: Backsteinhaus mit Garten und Gehweg"></div>

<!-- footer -->
<svg class="abs footer-bg" viewBox="0 0 1200 480" preserveAspectRatio="none">
  <path d="M0 40Q300 -10 600 40Q900 -10 1200 40V480H0Z" fill="#6aac1f"/>
</svg>
<div class="abs f-brand"><div class="mark"></div><div class="name">TOURISMUSVERBAND<br>KELBACH</div></div>
<div class="abs f-contact">
  <h4>Kontaktiere uns</h4>
  Tel.: 08599 / 401 2210<br>
  Fax: 08599 / 401 2219<br>
  info @ wanderhof-kelbach.de<br>
  Opening Hours: Mon-Fri 9:00 – 17:00<br>
  May-October: Sat 9:00-12:00
</div>
<div class="abs f-assoc">Fremdenverkehrsverein<br>Kelbach und Umgebung e.<br>V. Marktstraße 1</div>
<div class="abs f-rule"></div>
<div class="abs f-copy">Copyrights@2025.Tourismusverband. Alle Rechte vorbehalten</div>

</body>
</html>
```